BrivoTerna. Lantern of the Steady Harvest. Business card

Professional business card for BrivoTerna (Lantern of the Steady Harvest)
My rationale: Strategy-> Execution-> Results-> Value that lead to the BrivoTerna name: We put the Lantern of the Steady Harvest.
We deliver value to our customers helping them at defining a good strategy (cyan arrow). 90% of well formulated strategies fail due to poor execution so we also consider strategical execution very important (green arrow). Due to the execution we obtain the results (blue arrow). Finally, the results provide feedback to redefine strategy, and the new strategy has to be executed and new results obtained providing new feedback and on and on. It's like a wheel that finally, must create corporate value: value for shareholders, staholders, employees, providers...-

Target Market(s)

CEOs and steering comitees , invewrnent funds

Industry/Entity Type

Business Consultant

Contact Information for Business Card

Teodoro Vinsquel
CEO & Founder
teodoro.vinsquel@brivoterna-example.com
Mobile: +34 655.803.912
www.brivoterna-example.com

Colors

Designer to choose colors to be used in the design.

Requirements
Nice to have
• Nice to hace the words: Strategy, execution, results
• Nice to vave the claim: Lantern of the Steady Harvest
• The three colors should be shown:
• cyan for STRATEGY
• green for EXECUTION
• blue for RESULTS
Should not have
• Complete black background

```html
<!DOCTYPE html>
<html lang="en">
<head>
<meta charset="utf-8">
<title>BrivoTerna – Business Card</title>
<link rel="stylesheet" href="https://fonts.googleapis.com/css2?family=Archivo:wght@400;600;700&display=swap">
<style>
  :root{
    --page:#e8e5df;
    --paper:#f7f7f6;
    --navy:#1f3a91;
    --green:#86bc34;
    --cyan:#27a3d9;
    --back:#1f9fd4;
    --back-tone:#2aa6da;
    --ink:#2a2a2a;
    --white:#ffffff;
  }
  *{box-sizing:border-box;margin:0;padding:0}
  html,body{width:1200px;height:1200px;overflow:hidden;background:var(--page)}
  body{font-family:"Archivo",Arial,sans-serif;position:relative}
  .card{position:absolute;left:150px;width:900px;height:530px;box-shadow:0 8px 24px rgba(0,0,0,.18);overflow:hidden}
  .card--front{top:40px;background:var(--paper)}
  .card--back{top:630px;background:var(--back)}
  .card svg{display:block;width:900px;height:530px}
  .band-label{font-family:"Archivo",Arial,sans-serif;font-size:22px;fill:var(--white);font-weight:400;dominant-baseline:central}
  .brand{font-family:"Archivo",Arial,sans-serif;font-weight:700}
  .brand--front{font-size:40px;fill:var(--navy)}
  .brand--back{font-size:54px;fill:var(--white)}
  .name{font-family:"Archivo",Arial,sans-serif;font-size:32px;font-weight:600;fill:var(--navy)}
  .role{font-family:"Archivo",Arial,sans-serif;font-size:20px;font-weight:400;fill:var(--ink)}
  .contact{font-family:"Archivo",Arial,sans-serif;font-size:16px;font-weight:400;fill:var(--ink)}
  .icon{fill:none;stroke:var(--navy);stroke-width:2}
  .pattern-field{position:absolute;inset:0 0 140px 0;background:linear-gradient(135deg,var(--back-tone),var(--back))}
  .back-mark{position:absolute;inset:0}
</style>
</head>
<body>

<section class="card card--front" aria-label="Business card front">
  <svg viewBox="0 0 900 530" xmlns="http://www.w3.org/2000/svg">
    <!-- value stripes -->
    <polygon class="stripe stripe--strategy" points="-60,0 -20,0 171,530 131,530" fill="var(--cyan)"/>
    <polygon class="stripe stripe--execution" points="90,0 132,0 323,530 281,530" fill="var(--green)"/>
    <polygon class="stripe stripe--results" points="186,0 232,0 423,530 377,530" fill="var(--navy)"/>
    <polyline class="results-rise" points="400,540 550,200" stroke="var(--navy)" stroke-width="24" fill="none"/>
    <polygon class="name-band" points="562,200 900,200 900,300 516,300" fill="var(--green)"/>

    <text class="band-label" transform="translate(21,170) rotate(70.2)">Strategy</text>
    <text class="band-label" transform="translate(143,90) rotate(70.2)">Execution</text>
    <text class="band-label" transform="translate(234,70) rotate(70.2)">Results</text>

    <!-- brand -->
    <circle cx="346" cy="68" r="14" fill="var(--green)"/>
    <text class="brand brand--front" x="372" y="82">BrivoTerna</text>

    <!-- identity -->
    <text class="name" x="580" y="246">Teodoro Vinsquel</text>
    <text class="role" x="580" y="282">CEO &amp; Founder</text>

    <!-- contacts -->
    <g class="contact-row">
      <path class="icon" d="M492 354 q-4 8 4 16 q8 8 16 4 l-4-6 q-4 2-8-2 q-4-4-2-8 z"/>
      <text class="contact" x="524" y="368">+34 655.803.912</text>
    </g>
    <g class="contact-row">
      <rect class="icon" x="490" y="398" width="24" height="16"/>
      <polyline class="icon" points="490,398 502,408 514,398"/>
      <text class="contact" x="524" y="411">teodoro.vinsquel@brivoterna-example.com</text>
    </g>
    <g class="contact-row">
      <circle class="icon" cx="502" cy="448" r="10"/>
      <line class="icon" x1="492" y1="448" x2="512" y2="448"/>
      <ellipse class="icon" cx="502" cy="448" rx="4" ry="10"/>
      <text class="contact" x="524" y="454">www.brivoterna-example.com</text>
    </g>
  </svg>
</section>

<section class="card card--back" aria-label="Business card back">
  <div class="pattern-field" role="img" aria-label="Faint repeating brand pattern across the cyan background"></div>
  <svg class="back-mark" viewBox="0 0 900 530" xmlns="http://www.w3.org/2000/svg">
    <circle cx="560" cy="440" r="18" fill="var(--white)"/>
    <text class="brand brand--back" x="592" y="459">BrivoTerna</text>
  </svg>
</section>

</body>
</html>
```